Design the Business card for NetVaultic

Business card required for a professional Cyber Security business.
Company Logo and Icon has already been provided however I would like other options for the logo and icon to compare to. Alternatively, please refine/enhance the image of the logo.icon I have already provided.

If you are going to use the provided logo and icon, I was thinking that the company raised Logo on White background would serve well on the front of the card. See attached. AND, a large company raised stand-alone icon to appear on black background on the back of the card with tagline 'Cyber Risk Management, Governance and Consulting' or 'Cyber Security for your Business' See attached.
Alternatively, provide your own design for the logo and icon.

Target Market(s)

Enterprise, Government, Financial.

Contact Information for Business Card

Tavin Orloweth
Founder and CEO

Email Address
Mobile Number
Website URL
LinkedIn URL

Logo Text

NetVaultic - see attached example of logo

Font styles to use
Other font styles liked:
• Berlin Sans FB

Requirements
Must have
• Clean large and bold icon on the back with tagline.
• Horizontal alignment,
Nice to have
• Round edges.
• Raised Logo/Icon
Should not have
• An unprofessional look and feel.

```html
<!DOCTYPE html>
<html lang="en">
<head>
<meta charset="utf-8">
<title>NetVaultic Business Card</title>
<link href="https://fonts.googleapis.com/css2?family=Arimo:wght@400;700&display=swap" rel="stylesheet">
<style>
  :root {
    --backdrop: #3b3431;
    --card: #0d0d0e;
    --brand-blue: #1a73c9;
    --name-blue: #4a78c6;
    --accent-yellow: #f4b719;
    --text-light: #e6e6e6;
    --divider: #2a2a2c;
  }
  * { box-sizing: border-box; margin: 0; padding: 0; }
  html, body {
    width: 1200px;
    height: 844px;
    overflow: hidden;
    background: var(--backdrop);
    font-family: "Arimo", Arial, sans-serif;
  }
  .stage {
    position: relative;
    width: 1200px;
    height: 844px;
  }
  .card {
    position: absolute;
    top: 272px;
    width: 520px;
    height: 300px;
    background: var(--card);
    border-radius: 10px;
    box-shadow: 0 10px 28px rgba(0,0,0,0.45);
    overflow: hidden;
  }
  .card-contact { left: 50px; }
  .card-brand { left: 630px; }

  /* Contact side */
  .brand-block {
    position: absolute;
    left: 0;
    top: 0;
    width: 250px;
    height: 300px;
    display: flex;
    align-items: center;
    justify-content: center;
    gap: 10px;
  }
  .brand-dot {
    width: 22px;
    height: 22px;
    border-radius: 50%;
    background: var(--accent-yellow);
  }
  .brand-name {
    font-weight: 700;
    font-size: 30px;
    color: var(--brand-blue);
  }
  .divider {
    position: absolute;
    left: 250px;
    top: 0;
    width: 1px;
    height: 300px;
    background: var(--divider);
  }
  .contact-block {
    position: absolute;
    left: 272px;
    top: 78px;
    color: var(--text-light);
  }
  .person-name {
    font-weight: 700;
    font-size: 19px;
    letter-spacing: 0.3px;
  }
  .person-name .first { color: var(--name-blue); }
  .person-name .last { color: var(--accent-yellow); }
  .person-title {
    font-size: 14px;
    margin-top: 2px;
  }
  .contact-list {
    list-style: none;
    margin-top: 30px;
  }
  .contact-list li {
    display: flex;
    align-items: center;
    gap: 8px;
    font-size: 14px;
    line-height: 21px;
  }
  .contact-icon {
    width: 12px;
    height: 12px;
    background: var(--accent-yellow);
    border-radius: 2px;
    display: flex;
    align-items: center;
    justify-content: center;
  }
  .contact-icon svg { width: 10px; height: 10px; }

  /* Brand side */
  .brand-front {
    position: absolute;
    left: 0;
    top: 0;
    width: 520px;
    height: 300px;
  }
  .front-mark {
    position: absolute;
    left: 96px;
    top: 98px;
    display: flex;
    align-items: center;
    gap: 14px;
  }
  .front-mark .brand-dot { width: 34px; height: 34px; }
  .front-mark .brand-name { font-size: 48px; }
  .tagline {
    position: absolute;
    right: 60px;
    top: 190px;
    font-size: 14px;
    color: var(--text-light);
  }
</style>
</head>
<body>
<main class="stage">
  <section class="card card-contact">
    <div class="brand-block">
      <span class="brand-dot"></span>
      <span class="brand-name">NetVaultic</span>
    </div>
    <div class="divider"></div>
    <div class="contact-block">
      <p class="person-name"><span class="first">TAVIN</span> <span class="last">ORLOWETH</span></p>
      <p class="person-title">Founder and CEO</p>
      <ul class="contact-list">
        <li>
          <span class="contact-icon">
            <svg viewBox="0 0 10 10"><path d="M2 1.5 L3.6 1.5 L4.2 3.4 L3.2 4.2 Q4 5.9 5.8 6.8 L6.6 5.8 L8.5 6.4 L8.5 8 Q4.5 8.6 2 5 Q1.3 3.4 2 1.5 Z" fill="#0d0d0e"/></svg>
          </span>
          055-987 321 460
        </li>
        <li>
          <span class="contact-icon">
            <svg viewBox="0 0 10 10"><rect x="1.5" y="2.5" width="7" height="5" fill="none" stroke="#0d0d0e" stroke-width="1"/><path d="M1.5 2.5 L5 5.3 L8.5 2.5" fill="none" stroke="#0d0d0e" stroke-width="1"/></svg>
          </span>
          info@mailsample.com
        </li>
        <li>
          <span class="contact-icon">
            <svg viewBox="0 0 10 10"><circle cx="5" cy="5" r="3.4" fill="none" stroke="#0d0d0e" stroke-width="1"/><path d="M1.6 5 H8.4 M5 1.6 Q3 5 5 8.4 M5 1.6 Q7 5 5 8.4" fill="none" stroke="#0d0d0e" stroke-width="0.8"/></svg>
          </span>
          www.vaultsample.com
        </li>
        <li>
          <span class="contact-icon"></span>
          www.profilepage.com
        </li>
      </ul>
    </div>
  </section>

  <section class="card card-brand">
    <div class="brand-front">
      <div class="front-mark">
        <span class="brand-dot"></span>
        <span class="brand-name">NetVaultic</span>
      </div>
      <p class="tagline">Cyber Security for your Business</p>
    </div>
  </section>
</main>
</body>
</html>
```